Website Redesign

This is a B2B (Mainly)/B2C website .

Vaporel (our manufacturer) only sells the Sprayer itself. As a result they rarely speak directly to the benefits of a disinfecting chemicals ie. Their marketing is more directed to how quickly the sprayer can cover a given area or how much disinfecting Chemical is saved by spraying instead of the 'spray and wipe method. Also how much labor is saved by spraying.

We will be selling both similar to brindlowash.com

1. Main Selling Point? Infectious disease control and prevention via Electromagnetic Disinfecting Sprayers. Upsell is chemicals used in the sprayer and other products for use in disinfection and cleaning.

Our price point is $1495 so sales generally happen after they speak to our sales team.

End user is in most cases a Business. In some cases an individual as well but 75% business, hospital, School district, Universities.

Redesign is meant to tell a much better story to customer by and presenting a cleaner design. Most important metric is increased conversions.

Number of Pages Required

5+ page

```html
<!DOCTYPE html>
<html lang="en">
<head>
<meta charset="utf-8">
<title>Norva Group — Electromagnetic Disinfecting Sprayers</title>
<link rel="stylesheet" href="https://fonts.googleapis.com/css2?family=Jost:wght@400;500;600&family=Poppins:wght@400;500&display=swap">
<style>
:root{
  --sky:#1aa6e4;
  --navy:#1565b0;
  --ink:#222;
  --body:#444;
  --mist:#f6f6f6;
  --night:#15171c;
  --white:#fff;
}
*{box-sizing:border-box;margin:0;padding:0}
html,body{width:1200px;height:3591px;overflow:hidden;background:var(--white)}
body{position:relative;font-family:'Poppins',sans-serif;color:var(--body)}
.abs{position:absolute}
.head-font{font-family:'Jost',sans-serif}
.brand{display:flex;align-items:center;gap:10px;font-family:'Jost',sans-serif;font-weight:600;font-size:26px;color:var(--navy);line-height:1}
.brand-dot{width:34px;height:34px;border-radius:50%;background:var(--sky)}
.btn{display:flex;align-items:center;justify-content:center;border-radius:30px;background:var(--sky);color:var(--white);font-family:'Jost',sans-serif;font-size:16px;text-transform:uppercase}
.btn-line{background:transparent;border:2px solid var(--white)}
/* header */
.contact{display:flex;align-items:center;gap:10px;font-size:17px;color:var(--ink)}
.contact-ico{width:40px;height:40px;border-radius:50%;background:var(--navy);display:flex;align-items:center;justify-content:center}
.nav{display:flex;gap:18px;font-size:15px;color:var(--ink);font-weight:500}
.nav a{padding:4px 14px;border-radius:18px}
.nav .on{background:#dff1fb}
/* hero */
.hero-title{font-family:'Jost',sans-serif;font-weight:600;font-size:60px;color:var(--white)}
.hero-sub{font-family:'Jost',sans-serif;font-size:29px;line-height:43px;color:var(--white)}
.price{border:3px solid var(--white);border-radius:40px;display:flex;align-items:center;gap:16px;padding-left:8px;font-family:'Jost',sans-serif;font-size:29px;color:var(--white)}
.price-ico{width:58px;height:58px;border-radius:50%;background:var(--white);display:flex;align-items:center;justify-content:center}
/* sections */
.eyebrow{font-family:'Jost',sans-serif;font-size:20px;color:var(--sky);text-transform:uppercase}
.title{font-family:'Jost',sans-serif;font-weight:600;font-size:40px;color:var(--navy);text-transform:uppercase;letter-spacing:-.5px}
.copy{font-size:14.5px;line-height:24px;color:var(--body)}
.ticks{list-style:none}
.ticks li{display:flex;align-items:center;gap:12px;height:33px;font-size:15.5px;color:var(--ink)}
.card{width:300px;text-align:center}
.card-ico{width:122px;height:122px;border-radius:50%;margin:0 auto;display:flex;align-items:center;justify-content:center}
.card h3{font-family:'Jost',sans-serif;font-weight:400;font-size:25px;margin-top:26px}
.card p{font-size:14px;line-height:24px;margin-top:10px}
.card .btn{width:114px;height:53px;margin:26px auto 0}
.footer h4{font-family:'Jost',sans-serif;font-weight:500;font-size:23px;color:var(--sky)}
.links a{display:block;font-size:14px;line-height:24px;color:var(--body)}
</style>
</head>
<body>

<!-- header -->
<header>
  <div class="abs brand" style="left:111px;top:40px"><span class="brand-dot"></span>NORVA GROUP</div>
  <div class="abs contact" style="left:692px;top:13px">
    <span class="contact-ico"><svg width="20" height="14" viewBox="0 0 20 14"><rect x="1" y="1" width="18" height="12" fill="none" stroke="#fff" stroke-width="1.6"/><path d="M1 1l9 7 9-7" fill="none" stroke="#fff" stroke-width="1.6"/></svg></span>
    info@norvagroup.com
    <span class="contact-ico" style="margin-left:8px;background:var(--sky)"><svg width="18" height="18" viewBox="0 0 24 24"><path d="M6.6 10.8a15 15 0 006.6 6.6l2.2-2.2c.3-.3.7-.4 1-.2 1.1.4 2.3.6 3.6.6.6 0 1 .4 1 1V20c0 .6-.4 1-1 1A17 17 0 013 4c0-.6.4-1 1-1h3.5c.6 0 1 .4 1 1 0 1.2.2 2.4.6 3.6.1.3 0 .7-.2 1z" fill="#fff"/></svg></span>
    <span style="color:var(--sky)">+123 555 0142</span>
  </div>
  <nav class="abs nav" style="right:112px;top:72px;gap:4px">
    <a class="on">HOME</a><a>ABOUT</a><a>PRODUCTS</a><a>INDUSTRIES</a><a>FAQ</a><a>NEWS &amp; VIEWS</a><a>CONTACT</a>
  </nav>
</header>

<!-- hero -->
<section class="abs" style="left:0;top:118px;width:1200px;height:746px">
  <svg class="abs" style="left:0;top:0" width="1200" height="746">
    <rect width="1200" height="746" fill="#1aa6e4"/>
    <polygon points="0,0 1200,0 1200,516 0,616" fill="#15171c"/>
  </svg>
  <div class="abs" role="img" aria-label="Handheld electromagnetic disinfecting sprayer, grey and white, on a starry dark background" style="left:704px;top:63px;width:397px;height:579px;border-radius:60px 60px 20px 20px;background:linear-gradient(160deg,#e9e9e9,#6b6f77 45%,#2a2c31)"></div>
  <h1 class="abs hero-title" style="left:109px;top:152px">NORVA GROUP</h1>
  <p class="abs hero-sub" style="left:110px;top:238px">Infectious Disease Control And Prevention Via<br>Electromagnetic Disinfecting Sprayers</p>
  <a class="abs btn btn-line" style="left:111px;top:357px;width:128px;height:57px;font-weight:500;font-size:18px;border-width:3px;background:transparent">READ MORE</a>
  <div class="abs price" style="left:111px;top:635px;width:424px;height:77px">
    <span class="price-ico"><svg width="36" height="36" viewBox="0 0 36 36"><circle cx="18" cy="18" r="14" fill="none" stroke="#1aa6e4" stroke-width="2.5"/><text x="18" y="24" text-anchor="middle" font-family="Poppins" font-size="17" fill="#1aa6e4">$</text></svg></span>
    Our price point is $1495
  </div>
</section>

<!-- about -->
<section>
  <div class="abs" role="img" aria-label="Black backpack disinfecting sprayer with hose and spray wand" style="left:111px;top:920px;width:433px;height:418px;border-radius:30px;background:linear-gradient(150deg,#4a4a4e,#1b1b1e)"></div>
  <p class="abs eyebrow" style="left:606px;top:957px">About</p>
  <h2 class="abs title" style="left:606px;top:980px">Norva Group</h2>
  <div class="abs" style="left:606px;top:1046px;width:482px">
    <p class="copy" style="text-align:justify">Duis aute irure dolor in reprehenderit in voluptate velit esse cillum dolore eu fugiat nulla pariatur. Excepteur sint occaecat cupidatat non proident.</p>
    <p class="copy" style="text-align:justify;margin-top:7px">Their marketing is more directed to how quickly the sprayer can cover a given area or how much disinfecting Chemical is saved by spraying instead of the 'spray and wipe method. Also how much labor is saved by spraying.</p>
  </div>
  <a class="abs btn" style="left:606px;top:1247px;width:114px;height:53px">Read More</a>
</section>

<!-- technologies -->
<section>
  <svg class="abs" style="left:0;top:1373px" width="1200" height="700"><polygon points="0,62 1200,0 1200,697 0,641" fill="#f6f6f6"/></svg>
  <p class="abs eyebrow" style="left:111px;top:1495px">Safer Chemicals</p>
  <h2 class="abs title" style="left:111px;top:1518px">Advanced Technologies.</h2>
  <p class="abs copy" style="left:111px;top:1584px;width:578px;text-align:justify">Duis aute irure dolor in reprehenderit in voluptate velit esse cillum dolore eu fugiat nulla pariatur. Excepteur sint occaecat cupidatat non proident. velit esse cillum dolore eu fugiat nulla pariatur.</p>
  <ul class="abs ticks" style="left:111px;top:1672px">
    <li><svg width="18" height="16" viewBox="0 0 18 16"><path d="M1 9l5 5L17 1" fill="none" stroke="#1aa6e4" stroke-width="3"/></svg>IMPROVE compliance standards</li>
    <li><svg width="18" height="16" viewBox="0 0 18 16"><path d="M1 9l5 5L17 1" fill="none" stroke="#1aa6e4" stroke-width="3"/></svg>ELIMINATE human error</li>
    <li><svg width="18" height="16" viewBox="0 0 18 16"><path d="M1 9l5 5L17 1" fill="none" stroke="#1aa6e4" stroke-width="3"/></svg>SIMPLIFY with safer technology and chemicals</li>
    <li><svg width="18" height="16" viewBox="0 0 18 16"><path d="M1 9l5 5L17 1" fill="none" stroke="#1aa6e4" stroke-width="3"/></svg>REDUCE outbreaks and HAI's</li>
    <li><svg width="18" height="16" viewBox="0 0 18 16"><path d="M1 9l5 5L17 1" fill="none" stroke="#1aa6e4" stroke-width="3"/></svg>BOOST worker happiness and success</li>
  </ul>
  <a class="abs btn" style="left:111px;top:1861px;width:114px;height:52px">Read More</a>
  <div class="abs" role="img" aria-label="Wheeled cart sprayer with tank and spray gun" style="left:850px;top:1456px;width:237px;height:523px;border-radius:24px;background:linear-gradient(180deg,#3a3a3e,#141416)"></div>
</section>

<!-- institutions -->
<section>
  <p class="abs eyebrow" style="left:0;width:1200px;text-align:center;top:2116px">Already at work in</p>
  <h2 class="abs title" style="left:0;width:1200px;text-align:center;top:2138px">Leading Institutions</h2>
  <p class="abs copy" style="left:118px;width:964px;text-align:center;top:2203px">Duis aute irure dolor in reprehenderit in voluptate velit esse cillum dolore eu fugiat nulla pariatur. Excepteur sint occaecat cupidatat non proi dent. velit esse cillum dolore eu fugiat nulla pariatur.</p>
  <div class="abs card" style="left:98px;top:2280px">
    <div class="card-ico" style="background:var(--sky)"><svg width="64" height="56" viewBox="0 0 64 56"><path d="M32 52S4 34 4 17A13 13 0 0132 10a13 13 0 0128 7c0 17-28 35-28 35z" fill="none" stroke="#fff" stroke-width="3"/><path d="M12 28h12l4-8 6 14 4-6h14" fill="none" stroke="#fff" stroke-width="3"/></svg></div>
    <h3 style="color:var(--sky)">Healthcare</h3>
    <p>Duis aute irure dolor in reprehenderit in voluptate velit esse cillum dolore eu fugiat nulla pariatur.</p>
    <a class="btn">Read More</a>
  </div>
  <div class="abs card" style="left:449px;top:2280px">
    <div class="card-ico" style="background:var(--navy)"><svg width="56" height="58" viewBox="0 0 56 58"><path d="M30 4h10v8l6 8v32a3 3 0 01-3 3H27a3 3 0 01-3-3V20l6-8z" fill="none" stroke="#fff" stroke-width="3"/><circle cx="12" cy="30" r="5" fill="none" stroke="#fff" stroke-width="3"/><circle cx="14" cy="44" r="3" fill="#fff"/></svg></div>
    <h3 style="color:var(--navy)">Chemical Disinfectants</h3>
    <p>Duis aute irure dolor in reprehenderit in voluptate velit esse cillum dolore eu fugiat nulla pariatur.</p>
    <a class="btn" style="background:var(--navy)">Read More</a>
  </div>
  <div class="abs card" style="left:802px;top:2280px">
    <div class="card-ico" style="background:var(--sky)"><svg width="60" height="60" viewBox="0 0 60 60"><circle cx="30" cy="30" r="26" fill="none" stroke="#fff" stroke-width="3"/><path d="M22 16v12m-4-12v10a4 4 0 008 0V16M22 30v16M38 16c-4 2-5 8-5 14h5v16" fill="none" stroke="#fff" stroke-width="3"/></svg></div>
    <h3 style="color:var(--sky)">Food services</h3>
    <p>Duis aute irure dolor in reprehenderit in voluptate velit esse cillum dolore eu fugiat nulla pariatur.</p>
    <a class="btn">Read More</a>
  </div>
</section>

<!-- news -->
<section>
  <div class="abs" role="img" aria-label="Worker spraying disinfectant mist in a school hallway with lockers" style="left:0;top:2711px;width:700px;height:474px;background:linear-gradient(120deg,#4b5660,#8c8f92 50%,#5d6369)"></div>
  <svg class="abs" style="left:0;top:2676px" width="1200" height="572">
    <polygon points="504,35 1200,0 1200,478 613,509" fill="#1565b0"/>
    <polygon points="613,509 1200,478 1200,571" fill="#1aa6e4"/>
  </svg>
  <p class="abs head-font" style="right:112px;top:2832px;font-size:19px;color:var(--white)">IN THE NEWS</p>
  <h2 class="abs title" style="right:112px;top:2856px;color:var(--white)">More Efficient</h2>
  <svg class="abs" style="left:667px;top:2848px" width="70" height="46"><path d="M24 4L6 23l18 19M46 4l18 19-18 19" fill="none" stroke="#fff" stroke-width="3"/></svg>
  <p class="abs head-font" style="left:620px;width:468px;top:2925px;font-size:18px;line-height:30px;color:var(--white);text-align:justify;text-align-last:right">Infectious disease control and prevention via Electromagnetic Disinfecting Sprayers. Upsell is chemicals used in the sprayer and other products for use in disinfection and cleaning.</p>
  <a class="abs btn btn-line" style="left:973px;top:3043px;width:114px;height:52px">Read More</a>
</section>

<!-- footer -->
<footer class="footer">
  <div class="abs brand" style="left:111px;top:3328px"><span class="brand-dot"></span>NORVA GROUP</div>
  <p class="abs copy" style="left:111px;top:3397px;width:315px;font-size:14px">Nemo enim ipsam voluptatem quia voluptas sit aspernatur aut odit aut fugit, sed quia con sequuntur magni dolores eos qui ratione vo luptatem sequi nesciunt.</p>
  <h4 class="abs" style="left:479px;top:3300px">Quick Links</h4>
  <div class="abs links" style="left:481px;top:3340px"><a>Home</a><a>About</a><a>Products</a><a>Industries</a><a>FAQ</a><a>Warranty</a></div>
  <div class="abs links" style="left:592px;top:3340px"><a>News &amp; Views</a><a>Contact</a><a>For More Information</a></div>
  <h4 class="abs" style="left:814px;top:3300px">Subscribe With Us</h4>
  <div class="abs" style="left:814px;top:3349px;width:273px;height:53px;border:1.5px solid #bbb;border-radius:30px;padding:0 16px;display:flex;align-items:center;font-size:14px;color:#555">Email Address</div>
  <a class="abs btn" style="left:814px;top:3412px;width:118px;height:52px;text-transform:none;font-weight:600;font-size:17px">Subscribe</a>
  <div class="abs" style="left:111px;top:3533px;width:977px;height:1px;background:#ccc"></div>
  <p class="abs" style="left:0;width:1200px;text-align:center;top:3558px;font-size:15px;color:var(--ink)">Copyrights @ 2020 Norva Group. All Rights Reserved.</p>
</footer>

</body>
</html>
```